Business Card Design for Mortgage Broking Business

We need to redesign the business card. Mortgage broking business, doing home loan and commercial loans, existing logo, also QLBT member logo. design style needs to be simple, professional, elegant.

once final, need to setup for a team of different names and contact details.

Industry/Entity Type

Loan

Contact Information for Business Card

Name; Mobile; Email; Address; Tel; Fax; Australian Credit Licence: 618204

```html
<!DOCTYPE html>
<html lang="en">
<head>
<meta charset="utf-8">
<title>Keystone Home Finance – Business Card</title>
<link rel="stylesheet" href="https://fonts.googleapis.com/css2?family=Montserrat:wght@600;700&family=Questrial&display=swap">
<style>
  :root {
    --page: #ececee;
    --card: #ffffff;
    --navy: #2e2a92;
    --cyan: #1ea6e3;
    --link-blue: #1f7fc4;
    --ink: #2a2a2a;
    --badge: #e3f0e0;
    --badge-edge: #2e2a92;
  }
  html, body {
    margin: 0;
    width: 1200px;
    height: 873px;
    overflow: hidden;
    background: var(--page);
  }
  .canvas {
    position: relative;
    width: 1200px;
    height: 873px;
  }
  .card {
    position: absolute;
    width: 620px;
    height: 354px;
    background: var(--card);
    box-shadow: 0 6px 18px rgba(0,0,0,0.18);
    overflow: hidden;
  }
  .card--front { left: 60px; top: 60px; }
  .card--back { left: 520px; top: 450px; }
  .card__bands {
    position: absolute;
    inset: 0;
    width: 620px;
    height: 354px;
  }
  .brand {
    position: absolute;
    display: flex;
    align-items: center;
    gap: 14px;
    font-family: "Montserrat", sans-serif;
    font-weight: 700;
    color: var(--navy);
    white-space: nowrap;
  }
  .brand__mark {
    background: var(--navy);
    flex: none;
  }
  .brand__name { line-height: 1.1; }
  .card--front .brand {
    left: 130px;
    top: 124px;
    font-size: 36px;
  }
  .card--front .brand__mark { width: 52px; height: 52px; }
  .card--back .brand {
    right: 36px;
    top: 214px;
    font-size: 24px;
  }
  .card--back .brand__mark { width: 32px; height: 32px; }
  .member-badge {
    position: absolute;
    right: 24px;
    top: 150px;
    width: 86px;
    height: 24px;
    background: var(--badge);
    border: 2px solid var(--badge-edge);
  }
  .person {
    position: absolute;
    right: 28px;
    top: 40px;
    width: 236px;
  }
  .person__name {
    background: var(--navy);
    color: #fff;
    font-family: "Montserrat", sans-serif;
    font-weight: 700;
    font-size: 17px;
    text-align: center;
    padding: 6px 0;
    border-radius: 5px;
  }
  .person__role {
    font-family: "Questrial", sans-serif;
    font-size: 15px;
    color: var(--ink);
    margin: 6px 0 0 8px;
  }
  .contact-rail {
    position: absolute;
    left: 28px;
    top: 150px;
    width: 40px;
    height: 168px;
    background: var(--navy);
    border-radius: 0 0 6px 6px;
    display: flex;
    flex-direction: column;
    align-items: center;
    justify-content: space-around;
    padding: 6px 0;
    box-sizing: border-box;
  }
  .contact-rail svg { width: 22px; height: 22px; }
  .contact-list {
    position: absolute;
    left: 82px;
    top: 148px;
    margin: 0;
    padding: 0;
    list-style: none;
    font-family: "Questrial", sans-serif;
    font-size: 16px;
    line-height: 1.2;
    color: var(--link-blue);
  }
  .contact-list li { margin-bottom: 14px; }
  .contact-list li:last-child { margin-bottom: 0; }
</style>
</head>
<body>
<main class="canvas">

  <section class="card card--front" aria-label="Card front">
    <svg class="card__bands" viewBox="0 0 620 354" aria-hidden="true">
      <rect x="0" y="0" width="300" height="9" fill="var(--cyan)"/>
      <path d="M280 0 H620 V16 H310 Q296 16 290 6 Z" fill="var(--navy)"/>
      <path d="M0 340 H400 Q412 340 418 348 L422 354 H0 Z" fill="var(--navy)"/>
      <path d="M430 354 Q436 342 450 342 H620 V354 Z" fill="var(--cyan)"/>
    </svg>
    <div class="brand"><span class="brand__mark"></span><span class="brand__name">Keystone<br>Home Finance</span></div>
    <div class="member-badge" aria-label="QLBT member badge"></div>
  </section>

  <section class="card card--back" aria-label="Card back">
    <svg class="card__bands" viewBox="0 0 620 354" aria-hidden="true">
      <rect x="0" y="0" width="270" height="9" fill="var(--cyan)"/>
      <path d="M250 0 H620 V16 H280 Q266 16 260 6 Z" fill="var(--navy)"/>
      <path d="M0 340 H420 Q432 340 438 348 L442 354 H0 Z" fill="var(--navy)"/>
      <path d="M450 354 Q456 342 470 342 H620 V354 Z" fill="var(--cyan)"/>
    </svg>

    <div class="person">
      <div class="person__name">Daniel R. Hale</div>
      <div class="person__role">Financial Consultant</div>
    </div>

    <div class="contact-rail" aria-hidden="true">
      <svg viewBox="0 0 24 24" fill="none" stroke="#fff" stroke-width="2"><rect x="6" y="2" width="12" height="20" rx="2"/><line x1="10" y1="18" x2="14" y2="18"/></svg>
      <svg viewBox="0 0 24 24" fill="none" stroke="#fff" stroke-width="2"><circle cx="12" cy="12" r="9"/><path d="M3 12h18M12 3c3 3 3 15 0 18M12 3c-3 3-3 15 0 18"/></svg>
      <svg viewBox="0 0 24 24" fill="none" stroke="#fff" stroke-width="2"><rect x="3" y="6" width="18" height="12"/><path d="M3 6l9 7 9-7"/></svg>
      <svg viewBox="0 0 24 24" fill="#fff"><path d="M12 2a7 7 0 0 0-7 7c0 5 7 13 7 13s7-8 7-13a7 7 0 0 0-7-7zm0 9.5a2.5 2.5 0 1 1 0-5 2.5 2.5 0 0 1 0 5z"/></svg>
    </div>

    <ul class="contact-list">
      <li>07 3184 6290</li>
      <li>www.khf.com</li>
      <li>hello@khf.com</li>
      <li>27 Ardent Lane,<br>Milton QLD 4064</li>
    </ul>

    <div class="brand"><span class="brand__mark"></span><span class="brand__name">Keystone Home Finance</span></div>
  </section>

</main>
</body>
</html>
```